Allied Health team of Physiotherapists & Occupational Therapists seek a business card design

We have our new logo, we now need our new business cards and stationary. Tidewell: Oedema & Family Clinic is seeking a generic card design to represent our whole team and individual cards for each therapist that incorporates our new logo to communicate our holistic approach that is calming, nuturing, supportive and welcoming.
Our Physiotherapists and Occupational Therapists assess, treat and provide education for people who are at risk of or who have lymphoedema. This is often as a result of treatment for cancer. We provide pre-operative and post-operative management and cancer rehabilitation in our Pilates studio. Our team also consists of Physiotherapists who have a strong interest in pelvic floor and continence management for both men and women.

Target Market(s)

Mainly women health conscious

Industry/Entity Type

Allied Health: Physiotherapy / Occupational Therapy

Contact Information for Business Card

Address: 14 Gallivant Ave Larkmont 3274 Phone: 84316570 fax: 8431 6578 Email: info@tidewellcareservices.com.au Website: tidewellcareservices.com.au Facebook address: facebook.com/TidewellOedemaAndFamilyCareClinic. Room to write appointments. Individual cards need to have name, office email and individual email and professional details

Requirements
Must have
• Logo as per uploaded documents

```html
<!DOCTYPE html>
<html lang="en">
<head>
<meta charset="utf-8">
<title>Tidewell Business Card</title>
<link rel="stylesheet" href="https://fonts.googleapis.com/css2?family=Nunito+Sans:ital,wght@0,300;0,400;0,700;1,800&family=Philosopher:wght@700&display=swap">
<style>
  :root {
    --bg: #2b2b2b;
    --paper: #ffffff;
    --peach: #f9b17f;
    --peach-text: #f6a877;
    --sage: #c5cdc0;
    --dots: #6f6f6f;
  }
  html, body {
    margin: 0;
    width: 1200px;
    height: 1200px;
    overflow: hidden;
    background: var(--bg);
  }
  .canvas {
    position: relative;
    width: 1200px;
    height: 1200px;
  }
  .card {
    position: absolute;
    left: 160px;
    width: 880px;
    height: 503px;
    border-radius: 24px;
    overflow: hidden;
    background: var(--paper);
    box-shadow: 0 14px 30px rgba(0,0,0,0.45);
  }
  .card--front { top: 67px; }
  .card--back  { top: 630px; }
  .card svg { display: block; width: 100%; height: 100%; }
  .body-font { font-family: "Nunito Sans", sans-serif; }
  .holder-name { font-family: "Philosopher", serif; font-weight: 700; font-size: 27px; fill: var(--paper); }
  .role { font-size: 17px; font-weight: 400; fill: var(--paper); }
  .contact { font-size: 19px; font-weight: 300; fill: var(--paper); }
  .brand-name { font-size: 50px; font-weight: 300; fill: var(--peach); }
  .brand-sub { font-size: 15px; font-weight: 300; fill: var(--peach); letter-spacing: 2px; }
  .appt-title { font-size: 29px; font-weight: 400; fill: var(--peach-text); }
  .book-label { font-size: 18px; font-weight: 800; font-style: italic; fill: var(--paper); }
  .appt-label { font-size: 17px; font-weight: 400; fill: var(--peach-text); }
  .fill-line { stroke: var(--dots); stroke-width: 1.3; stroke-dasharray: 0.1 3; stroke-linecap: round; }
  .footer-url { font-size: 19px; font-weight: 400; fill: var(--paper); letter-spacing: 4.5px; }
  .brand-faint { font-size: 86px; font-weight: 300; fill: var(--peach); opacity: 0.13; }
</style>
</head>
<body>
<main class="canvas">

  <section class="card card--front" aria-label="Business card front">
    <svg viewBox="0 0 800 457" class="body-font">
      <path d="M0,197 Q400,420 800,210 L800,457 L0,457 Z" fill="var(--sage)"/>
      <path d="M0,217 Q400,442 800,214 L800,457 L0,457 Z" fill="var(--peach)"/>
      <path d="M0,217 Q400,442 800,214" fill="none" stroke="var(--paper)" stroke-width="2"/>

      <g class="brand-mark">
        <circle cx="400" cy="80" r="7" fill="var(--peach)"/>
        <text class="brand-name" x="400" y="165" text-anchor="middle">Tidewell</text>
        <text class="brand-sub" x="400" y="195" text-anchor="middle">OEDEMA &amp; FAMILY CLINIC</text>
      </g>

      <text class="holder-name" x="44" y="344">Maren Ellery</text>
      <text class="role" x="44" y="369">Physiotherapist</text>
      <text class="contact" x="40" y="404">14 Gallivant Ave</text>
      <text class="contact" x="40" y="429">Larkmont 3274</text>

      <g text-anchor="end">
        <text class="contact" x="755" y="353">(P) 8431 6570</text>
        <text class="contact" x="755" y="379">(F)8431 6578</text>
        <text class="contact" x="755" y="404">info@tidewellcareservices.com.au</text>
        <text class="contact" x="755" y="429">tidewellcareservices.com.au</text>
      </g>
    </svg>
  </section>

  <section class="card card--back" aria-label="Business card back">
    <svg viewBox="0 0 800 457" class="body-font">
      <text class="brand-faint" x="400" y="285" text-anchor="middle">Tidewell</text>

      <text class="appt-title" x="65" y="83">Next Appointment</text>
      <rect x="594" y="51" width="155" height="32" rx="8" fill="var(--peach)"/>
      <text class="book-label" x="671.5" y="73" text-anchor="middle">Book Online</text>

      <g class="appt-rows">
        <text class="appt-label" x="67" y="162">Date :</text>
        <line class="fill-line" x1="142" y1="160" x2="438" y2="160"/>
        <text class="appt-label" x="440" y="162">Time :</text>
        <line class="fill-line" x1="502" y1="160" x2="665" y2="160"/>
        <text class="appt-label" x="674" y="162">AM/PM</text>

        <text class="appt-label" x="67" y="212">Date :</text>
        <line class="fill-line" x1="142" y1="210" x2="438" y2="210"/>
        <text class="appt-label" x="440" y="212">Time :</text>
        <line class="fill-line" x1="502" y1="210" x2="665" y2="210"/>
        <text class="appt-label" x="673" y="212">AM/PM</text>

        <text class="appt-label" x="67" y="272">Date :</text>
        <line class="fill-line" x1="142" y1="270" x2="438" y2="270"/>
        <text class="appt-label" x="440" y="272">Time :</text>
        <line class="fill-line" x1="502" y1="270" x2="665" y2="270"/>
        <text class="appt-label" x="673" y="272">AM/PM</text>

        <text class="appt-label" x="67" y="332">Date :</text>
        <line class="fill-line" x1="142" y1="330" x2="438" y2="330"/>
        <text class="appt-label" x="440" y="332">Time :</text>
        <line class="fill-line" x1="502" y1="330" x2="665" y2="330"/>
        <text class="appt-label" x="673" y="332">AM/PM</text>
      </g>

      <rect x="0" y="377" width="800" height="39" fill="var(--peach)"/>
      <text class="footer-url" x="400" y="404" text-anchor="middle">TIDEWELLCARESERVICES.COM.AU</text>
    </svg>
  </section>

</main>
</body>
</html>
```